Business card design for holistic health care clinic

We need a double-sided business card design for our holistic health care clinic that integrates our logo design and also its color scheme. My business is called Valmira. It is an integrative medicine clinic. You have already done the logo for me. Please ensure an elegant and upscale design that is not cluttered, but still has all the necessary information (please see below for details).

Target Market(s)

Wellness, fitness, rehabilitation for educated, well-traveled open-minded clients who are focused on natural, organic, balanced and preventive healthcare and lifestyle.

Industry/Entity Type

Medical

Contact Information for Business Card

Modern, clean.

Number of Pages Required

1 page

Font styles to use
Serif
Sans Serif

Colors

Designer to choose colors to be used in the design.

Requirements
Must have
• Logo on one side, all other information on the other side.
• Other information should include:
• Tobias Wrenfeld - DOE, CPT, LMT
• 4100 East Marrow Drive
• Austin, TX 78119
• 512 555 0148
• 818 555 0192
• info@ValmiraHealth.example
• t.wrenfeld@ValmiraHealth.example
Nice to have
• Darker background on front - but not totally black - shaded/dark gray.

```html
<!DOCTYPE html>
<html lang="en">
<head>
<meta charset="utf-8">
<title>Valmira – Business Card</title>
<link href="https://fonts.googleapis.com/css2?family=Montserrat:wght@600;700&family=Work+Sans:wght@300;400&display=swap" rel="stylesheet">
<style>
  :root {
    --page-bg: #e4ddd5;
    --card-frost: #efebe6;
    --band: #3a3a3b;
    --teal: #2a93a6;
    --teal-dark: #1f7f93;
    --text-light: #d9d6d2;
    --text-muted: #c9c5c0;
  }
  * { margin: 0; padding: 0; box-sizing: border-box; }
  html, body {
    width: 1200px; height: 1047px; overflow: hidden;
    background: var(--page-bg);
  }
  .card {
    position: absolute; left: 80px; top: 241px;
    width: 1040px; height: 565px;
    border-radius: 22px; overflow: hidden;
    background: var(--card-frost);
    box-shadow: 0 10px 30px rgba(0,0,0,.12);
  }
  .brand { position: absolute; left: 60px; top: 104px; }
  .brand-name {
    font-family: "Montserrat", sans-serif; font-weight: 700;
    font-size: 82px; letter-spacing: 1px; line-height: 1;
    color: var(--teal);
  }
  .brand-tagline {
    margin-top: 18px; margin-left: 4px;
    font-family: "Montserrat", sans-serif; font-weight: 600;
    font-size: 24px; color: var(--teal);
  }
  .info-band {
    position: absolute; left: 0; right: 0; top: 290px; bottom: 0;
    background: var(--band);
  }
  .person { position: absolute; left: 54px; top: 30px; }
  .person-name {
    font-family: "Montserrat", sans-serif; font-weight: 600;
    font-size: 37px; color: var(--teal); letter-spacing: .5px;
  }
  .person-credentials {
    margin-top: 6px;
    font-family: "Work Sans", sans-serif; font-weight: 300;
    font-size: 21px; color: var(--text-muted); letter-spacing: 1px;
  }
  .contacts {
    position: absolute; left: 54px; top: 128px; list-style: none;
    font-family: "Work Sans", sans-serif; font-weight: 300;
    font-size: 23px; color: var(--text-light);
  }
  .contacts li { display: flex; align-items: center; height: 32px; }
  .contacts svg { width: 18px; height: 18px; margin-right: 14px; flex: none; }
  .address {
    position: absolute; right: 340px; top: 192px; text-align: right;
    font-family: "Work Sans", sans-serif; font-weight: 300;
    font-size: 23px; line-height: 32px; color: var(--text-muted);
  }
  .brand-mark {
    position: absolute; right: 90px; top: 50px;
    width: 170px; height: 170px; border-radius: 50%;
    background: var(--teal);
  }
</style>
</head>
<body>
  <div class="card">
    <div class="brand">
      <div class="brand-name">VALMIRA</div>
      <div class="brand-tagline">Integrative Holistic Medicine</div>
    </div>

    <div class="info-band">
      <div class="person">
        <div class="person-name">TOBIAS WRENFELD</div>
        <div class="person-credentials">DOE, CPT, LMT</div>
      </div>

      <ul class="contacts">
        <li>
          <svg viewBox="0 0 24 24" fill="none" stroke="#2a93a6" stroke-width="2"><path d="M5 3h4l2 5-2.5 1.5a11 11 0 0 0 6 6L16 13l5 2v4a2 2 0 0 1-2 2A16 16 0 0 1 3 5a2 2 0 0 1 2-2z"/></svg>
          512 555 0148
        </li>
        <li>
          <svg viewBox="0 0 24 24" fill="none" stroke="#2a93a6" stroke-width="2"><rect x="7" y="2" width="10" height="20" rx="2"/><line x1="11" y1="18" x2="13" y2="18"/></svg>
          818 555 0192
        </li>
        <li>
          <svg viewBox="0 0 24 24" fill="none" stroke="#2a93a6" stroke-width="2"><rect x="3" y="5" width="18" height="14" rx="1"/><path d="M3 6l9 7 9-7"/></svg>
          info@ValmiraHealth.example
        </li>
        <li>
          <svg viewBox="0 0 24 24" fill="none" stroke="#2a93a6" stroke-width="2"><circle cx="12" cy="12" r="9"/><path d="M3 12h18M12 3c3 3 3 15 0 18M12 3c-3 3-3 15 0 18"/></svg>
          t.wrenfeld@ValmiraHealth.example
        </li>
      </ul>

      <div class="address">
        4100 East Marrow Drive<br>
        Austin, TX 78119
      </div>

      <div class="brand-mark" aria-hidden="true"></div>
    </div>
  </div>
</body>
</html>
```